Quill Ride Business Cards

**As soon as there are some quality ideas presented, I will guarantee payment**

We require a template business card with 3 variations based on the following roles:

**Driver Specific version
Communicate;

-More customers, tips, safety, money
-GPS enabled
-no commitment required
-WE PAY YOU (first 3 months)
-Signup here: www.quillride.ca/drivers
-Incorporate QR code - provided
-Customer ratings
-Brokerage independent

**Staff Specific version
Communicate;

-www.quillride.ca
-GPS enabled hailing solution
-Taxis, Limosines, Town Cars
-Name, phone, email

**Customer Specific version
Communicate;
-www.quillride.ca
-Free Service
-Driver ratings
-No busy signals

Logo - provided
Main colours - Black, Yellow
Double sided card
Updates

Thanks for all the submissions, as promised, now that there are some sufficiently creative submissions I have guaranteed this project.  I will be giving some feedback and additional direction today.

Thanks,
Doug

A couple additional requirements;

The "customer" card will require 2 QR codes on it.  1 for iPhone app install and the other for Android app install.

All QR codes need to be at least 3.2cm x 3.2cm

Reason: Reason for extension is that I've gotten busy with another aspect of my business and haven't been able to provide feedback in a timely manner. Hence none of the designs are currently developed to the point that I'm ready to close the contest. PLEASE re-read the design brief to ensure you are addressing the requirements!

Industry/Entity Type

Business

Requirements
Must have
• The full logo on at least one side of the card. Just "QuillRide" text on the other is fine.

QR code integrated into card design

Clean and Simple design with high contrast
Should not have
• cluttered or overly ornate / fancy text

```html
<!DOCTYPE html>
<html lang="en">
<head>
<meta charset="utf-8">
<title>QuillRide Business Card</title>
<link rel="stylesheet" href="https://fonts.googleapis.com/css2?family=Open+Sans:wght@400;700;800&family=PT+Sans:ital,wght@1,700&display=swap">
<style>
  :root {
    --bg: #e9e7e2;
    --card-black: #231f20;
    --card-dark: #3b3a3a;
    --taxi-yellow: #f3e21b;
    --deep-yellow: #d9c400;
    --white: #ffffff;
    --ink: #1c1a1a;
  }
  * { margin: 0; padding: 0; box-sizing: border-box; }
  html, body {
    width: 1200px; height: 900px; overflow: hidden;
    background: var(--bg);
    font-family: "Open Sans", Arial, sans-serif;
  }
  .card {
    position: absolute; top: 294px;
    width: 537px; height: 306px;
    border-radius: 14px; overflow: hidden;
    background: var(--card-black);
  }
  .card--front { left: 60px; }
  .card--back {
    left: 626px;
    background: radial-gradient(ellipse at 50% 40%, var(--card-dark) 0%, var(--card-black) 75%);
  }

  /* front */
  .wordmark {
    position: absolute; left: 43px; top: 40px;
    font-weight: 800; font-size: 56px; letter-spacing: -1px;
    color: var(--white); line-height: 1;
  }
  .person {
    position: absolute; left: 56px; top: 124px;
    color: var(--white); display: flex; align-items: baseline; gap: 8px;
  }
  .person__name { font-weight: 700; font-size: 19px; }
  .person__role { font-size: 12px; }
  .front-band {
    position: absolute; left: 0; right: 0; top: 160px; bottom: 0;
    background: var(--taxi-yellow);
  }
  .contact {
    position: absolute; left: 56px; list-style: none;
    color: var(--ink); font-size: 13px;
  }
  .contact li { display: flex; align-items: center; gap: 8px; height: 20px; }
  .contact svg { width: 12px; height: 12px; }
  .contact--phones { top: 183px; }
  .contact--email { top: 240px; }
  .band-pattern {
    position: absolute; left: 0; right: 0; bottom: 0; height: 31px;
    background: linear-gradient(180deg, #6b6200 0%, var(--deep-yellow) 50%, #6b6200 100%);
  }
  .taxi-art {
    position: absolute; left: 298px; top: 88px;
    width: 236px; height: 212px; border-radius: 40px 40px 24px 24px;
    background: linear-gradient(180deg, var(--card-black) 0%, var(--taxi-yellow) 45%, var(--deep-yellow) 100%);
  }

  /* back */
  .logo-lockup {
    position: absolute; left: 0; right: 0; top: 90px;
    display: flex; justify-content: center; align-items: center; gap: 12px;
  }
  .logo-lockup__dot {
    width: 26px; height: 26px; border-radius: 50%;
    background: var(--taxi-yellow);
  }
  .logo-lockup__name {
    font-weight: 800; font-size: 40px; color: var(--taxi-yellow); line-height: 1;
  }
  .tagline {
    position: absolute; left: 0; right: 0; top: 210px;
    text-align: center; color: var(--taxi-yellow);
    font-family: "PT Sans", Arial, sans-serif;
    font-style: italic; font-weight: 700; font-size: 18px; line-height: 25px;
  }
</style>
</head>
<body>
  <section class="card card--front">
    <div class="wordmark">QuillRide</div>
    <div class="person">
      <span class="person__name">Nora Whitfield</span>
      <span class="person__role">| Admin Staff</span>
    </div>
    <div class="front-band"></div>
    <ul class="contact contact--phones">
      <li>
        <svg viewBox="0 0 12 12" aria-hidden="true"><path d="M1 4c0-2 1-3 5-3s5 1 5 3l-2 1-1-2H4L3 5zM2 6h8l1 5H1z" fill="#1c1a1a"/></svg>
        <span>555.210.483</span>
      </li>
      <li>
        <svg viewBox="0 0 12 12" aria-hidden="true"><path d="M1 4c0-2 1-3 5-3s5 1 5 3l-2 1-1-2H4L3 5zM2 6h8l1 5H1z" fill="#1c1a1a"/></svg>
        <span>555.318.6042</span>
      </li>
    </ul>
    <ul class="contact contact--email">
      <li>
        <svg viewBox="0 0 12 12" aria-hidden="true"><rect x="0.75" y="2.25" width="10.5" height="7.5" fill="none" stroke="#1c1a1a" stroke-width="1.2"/><path d="M1 2.5l5 4 5-4" fill="none" stroke="#1c1a1a" stroke-width="1.2"/></svg>
        <span>nwhitfield@quillride.ca</span>
      </li>
    </ul>
    <div class="band-pattern" role="img" aria-label="Black and yellow checkered taxi band"></div>
    <div class="taxi-art" role="img" aria-label="Illustration of a yellow taxi front with a signal beacon on its roof"></div>
  </section>

  <section class="card card--back">
    <div class="logo-lockup">
      <span class="logo-lockup__dot"></span>
      <span class="logo-lockup__name">QuillRide</span>
    </div>
    <p class="tagline">GPS enabled hailing solution<br>Taxis, Limosines, Town Cars</p>
    <div class="band-pattern" role="img" aria-label="Black and yellow checkered taxi band"></div>
  </section>
</body>
</html>
```